Small Business Directory Site Requires a Professional Responsive Web Design

Small Business Directory and Coupon Site - we require a complete website design for a brand new responsive & mobile friendly website. We already have a coder who will professional code our website in Magento.

All PSD pages need to be professionally designed then uploaded into a sharedrive (i.e. like filecrate). Additionally, as I cannot pre-empt everything, please note that we may require a little more assistance once the files have been transferred (for example, in www.brightlane-listings.example if you hover your mouse on the search box you will see a pop up box. We want one of these too and I think that means there may be extra design work here)

We have some draft page sketches have been created (there are some minor changes we want to the sketches provided though); however, we require an excellent designer to add the creative touches to it to make it look professionally created. All artwork/font must be legal.

-------------------------
We like the look of the www.brightlane-listings.example and www. marlowfolio.example

For the headers, please consider a font similar to RNS camellia. We likes this style, but it is too thin for the headers...so we need a variation like this one. For the copy/general text font, something basic that marries well with the headers.

---------------------

Please be sure to also read the brief we wrote for the coder as this will help with better understanding our design requirements.

In total I believe we have about 50 pages. This includes all the little pages and most of the pop up boxes (but not the little help key boxes). For example, pages include...

1. Login (this is where customers log in and can edit, manage their profiles. This means that there are backend membership pages)
2. Mini Services (same look and feel as the business coupons)
3. Resource Centre
4. Join (this is where customers learn about the packages available to submit a directory listing, if they ‘buy’ a package (i.e. free, $25 or $150 package) then they can create their own directory listing)
5. Search the directory (customer can view all the categories and also search the directory)
6. Create a directory listing (this is where customers learn about the packages available to submit a directory listing, if they ‘buy’ a package (i.e. free, $25 or $150 package) then they can create their own directory listing)
7. Quote finder (also know as Get a Quote)
8. Coupons (customer go to the business coupon page and can view all current coupons/submit a coupon)
9. Submit a coupon (form)
10.Advertise with us (form)
11. Join the forum
12.Submit an article or video (form)
13. Affiliates (listing of affiliates we currently have)
14. Become an affiliate (form)
15. Case studies (customer can view the case studies we have in the resource centre)
16. Help Guides (customer can view the help guides we have in the resource centre)
17. About Us
18 .Contact Us (form)
19. Terms & Condition
20. Privacy Policy
21. Supporting City Councils
22. Site Map
23. Forgot password / login details
24. Homepage
25. If we hover over a few areas (i.e. search box, location field) it pops up with more information.
etc etc etc. . . there are more pages.

Please see our filecrate link for the draft mock up pages that I have created so far.

https://www.cloudtrunk.example/sh/qk72pmw4rtz8nd/KLMvbTq2fWndxPzs8Yh4ecRQu

We are in a rush! We'd like to get the majority of the artwork completed by the end of the month. Minor fixes/tweaks can occur thereafter.

Target Market(s)

Small Businesses (employees 0 - 50) located throughout Australia

Industry/Entity Type

Business

Font styles to use
Sans Serif

Requirements
Must have
• Professional. Artwork must be legal (cannot be cut and paste or taken off other websites, must be legally purchased and used).Must look contemporary, fresh, modern.

Absolutely must be a responsive site!
Nice to have
• original work, original photos, original art.

like modern, fresh photos that demonstrate innovation, growth, small business, Australian scenery, stability, goals/passion.
Should not have
• cut and paste graphics, illegal graphics, not purchased graphics.

```html
<!DOCTYPE html>
<html lang="en">
<head>
<meta charset="utf-8">
<title>Wattle Business Link – Australia's Small Business Directory</title>
<link href="https://fonts.googleapis.com/css2?family=Questrial&family=Open+Sans:wght@400;600;700&display=swap" rel="stylesheet">
<style>
:root{
  --orange:#f7931e;
  --cyan:#29abe2;
  --green:#6cb33f;
  --yellow:#ffe21a;
  --black:#0d0d0d;
  --dark:#1b1b1b;
  --ink:#333;
  --muted:#8a8a8a;
  --line:#dcdcdc;
  --white:#fff;
}
*{box-sizing:border-box;margin:0;padding:0}
html,body{width:1200px;height:3147px;overflow:hidden}
body{position:relative;background:var(--white);font-family:"Open Sans",Arial,sans-serif;color:var(--ink);font-size:14px}
.abs{position:absolute}
.display{font-family:"Questrial","Century Gothic",sans-serif;font-weight:400}
a{color:inherit;text-decoration:none}

/* header */
.site-header{left:0;top:0;width:1200px;height:109px;background:var(--black)}
.brand{left:120px;top:36px;display:flex;align-items:center;gap:12px}
.brand-mark{width:64px;height:44px;background:var(--orange);border:3px solid #fff}
.brand-name{color:#fff;font-size:22px;font-weight:600;letter-spacing:.5px}
.top-links{right:240px;top:8px;color:#fff;font-size:11px;display:flex;gap:6px;white-space:nowrap}
.account{left:974px;top:0;width:112px;height:30px;background:var(--cyan);color:#fff;font-weight:700;font-size:13px;display:flex;justify-content:center;align-items:center;gap:12px}
.social{left:965px;top:54px;display:flex;gap:6px}
.social span{width:19px;height:19px;border-radius:2px}

/* hero */
.hero{left:0;top:109px;width:1200px;height:552px;background:linear-gradient(180deg,#7fb6de 0%,#c9e0ee 40%,#d7d9a2 62%,#a3a24a 80%,#6a7a2c 100%)}
.hero-title{left:115px;top:293px;color:#1d1d1d;font-size:36px;line-height:46px}
.search{left:115px;top:392px;width:504px;height:44px;background:var(--orange);padding:5px;display:flex;gap:6px}
.search .field{background:#fff;height:34px;font-size:12px;color:#555;padding:9px 10px}
.search .what{width:210px}.search .where{width:210px}
.search .go{width:52px;height:34px;background:var(--black);margin-left:auto;display:flex;align-items:center;justify-content:center}
.listing{left:814px;top:231px;width:239px;height:314px;background:#fff;box-shadow:0 3px 10px rgba(0,0,0,.25);text-align:center}
.listing-head{background:var(--orange);color:#fff;font-size:13px;height:35px;line-height:35px}
.listing-price{font-size:22px;color:#333;margin-top:12px}
.listing-photo{margin:10px auto 0;width:105px;height:100px;background:linear-gradient(135deg,#cfcfcf,#8b8b8b)}
.listing-cap{font-size:8px;color:#777;margin-top:4px}
.listing-arrow{top:136px;width:0;height:0;border-top:9px solid transparent;border-bottom:9px solid transparent}
.listing-arrow.l{left:38px;border-right:10px solid var(--orange)}
.listing-arrow.r{right:38px;border-left:10px solid var(--orange)}
.listing-tier{color:var(--orange);font-size:13px;font-weight:600;margin-top:26px}
.listing-desc{font-size:11px;font-weight:600;color:#222;line-height:15px;margin-top:4px}
.stones{left:1060px;top:109px;width:140px;height:552px;background:linear-gradient(180deg,#c9a98a,#8d7864 60%,#6a5c4b)}
.categories{left:115px;top:619px;width:970px;height:42px;background:#fff;display:flex;align-items:center;padding:0 12px;gap:12px;font-size:11px;color:#222;white-space:nowrap}
.categories .active{border-bottom:2px solid var(--orange);padding-bottom:3px}
.categories .all{margin-left:auto;text-decoration:underline;font-weight:600}

/* featured */
.section-title{width:1200px;text-align:center;color:#111}
.section-sub{width:1200px;text-align:center;color:var(--muted);font-size:17px}
.rule{left:510px;width:180px;height:2px;background:var(--line)}
.card{top:881px;width:252px}
.card-img{height:180px}
.card-bar{height:42px;background:#2a2a2a;color:#fff;font-size:12px;font-weight:600;display:flex;align-items:center;justify-content:space-between;padding:0 10px;white-space:nowrap}
.card-text{font-size:12px;line-height:18px;color:#444;margin-top:14px;padding-right:6px}
.more{color:var(--orange);font-size:12px;margin-top:4px;display:flex;align-items:center;gap:4px}
.badge-grid{height:180px;background:#fff;display:grid;grid-template-columns:repeat(4,1fr);gap:12px;padding:10px}
.badge-grid span{background:#d9dde4;border-radius:3px}
.slide-arrow{width:28px;height:28px;border-radius:50%;border:2px solid #222;background:#fff;display:flex;align-items:center;justify-content:center}
.btn{color:#fff;font-size:12px;display:flex;align-items:center;justify-content:center;white-space:nowrap}

/* directory promo */
.promo{left:0;top:1357px;width:1200px;height:577px;background:radial-gradient(ellipse at center,#262626,#141414)}
.promo-title{color:var(--orange);font-size:46px}
.promo-sub{color:#9a9a9a}
.devices{left:250px;top:1570px;width:360px;height:270px;border-radius:18px;background:linear-gradient(135deg,#2c3640,#4d5a66 50%,#1f2429)}
.adv-head{left:671px;top:1618px;color:#fff;font-size:24px}
.adv-head b{color:var(--cyan);font-weight:400}
.adv-text{left:671px;top:1668px;width:440px;color:#ddd;font-size:13px;line-height:20px}
.adv-text strong{color:var(--orange);font-size:18px}
.start{left:671px;top:1752px;width:204px;height:34px;background:var(--cyan);color:#111;font-weight:600;font-size:13px;gap:10px}

/* join band */
.band{left:0;top:1934px;width:1200px;height:290px;background:linear-gradient(90deg,#3a352c,#6b5e45 30%,#4a4136 55%,#8a7a4c 80%,#524632)}
.band-col{top:2008px;width:280px;text-align:center;color:#fff}
.band-col h3{font-size:24px;font-weight:600;margin-bottom:10px}
.band-col p{font-size:12.5px;line-height:17px;color:#eee}
.band-btn{display:inline-block;margin-top:16px;background:var(--yellow);color:#111;font-weight:700;font-size:14px;padding:7px 20px}

/* get real support */
.polaroid{top:2465px;width:262px;height:273px}
.polaroid .frame{position:absolute;inset:0;background:#fff;box-shadow:0 2px 6px rgba(0,0,0,.25)}
.polaroid .frame.back1{transform:rotate(-4deg)}
.polaroid .frame.back2{transform:rotate(3deg)}
.polaroid .photo{position:absolute;left:20px;top:20px;width:222px;height:190px}
.polaroid .label{position:absolute;left:0;width:100%;top:222px;text-align:center;color:var(--cyan);font-size:20px}
.pol-date{width:262px;text-align:center;color:var(--orange);font-size:12px;top:2441px}
.pol-text{top:2788px;width:262px;text-align:center;font-size:12.5px;line-height:17px;color:#333}
.ring-arrow{width:22px;height:22px;border-radius:50%;border:1px solid #bbb;display:flex;align-items:center;justify-content:center}

/* footer */
.site-footer{left:0;top:2900px;width:1200px;height:209px;background:var(--black)}
.foot-col{top:2936px}
.foot-col h4{color:var(--orange);font-size:13px;font-weight:400;margin-bottom:10px}
.foot-col li{list-style:none;color:#ccc;font-size:11.5px;line-height:21px}
.foot-social{display:flex;gap:5px}
.foot-social span{width:24px;height:24px}
.coupon-btn{margin-top:14px;background:var(--orange);color:#fff;font-size:11px;font-weight:600;padding:7px 12px;display:inline-block}
.copyright{left:0;top:3109px;width:1200px;height:38px;background:#2b2b2b;color:#ddd;font-size:11px;text-align:center;line-height:38px}
</style>
</head>
<body>

<header class="abs site-header">
  <div class="abs brand"><span class="brand-mark"></span><span class="brand-name">Wattle Business Link</span></div>
  <nav class="abs top-links"><a>Coupons</a>|<a>Mini Service</a>|<a>Get a Quote</a>|<a>Advertise</a>|<a>Resource Centre</a></nav>
  <div class="abs account"><span>JOIN</span><span>LOGIN</span></div>
  <div class="abs social"><span style="background:#3fa9f5"></span><span style="background:#f26522"></span><span style="background:#3b5998"></span><span style="background:#0e76a8"></span><span style="background:#666"></span></div>
</header>

<section class="abs hero" role="img" aria-label="Sunlit field of tall grass under a blue sky with a hand stacking smooth stones"></section>
<div class="abs stones" role="img" aria-label="Balanced stack of stones"></div>
<h1 class="abs hero-title display">It's A Brand New Day.<br>Do More of what you love</h1>
<form class="abs search">
  <div class="field what">What are you looking for</div>
  <div class="field where">Near where?</div>
  <div class="go"><svg width="20" height="20" viewBox="0 0 20 20"><circle cx="8" cy="8" r="6" fill="none" stroke="#fff" stroke-width="2.5"/><line x1="12.5" y1="12.5" x2="18" y2="18" stroke="#fff" stroke-width="3"/></svg></div>
</form>
<aside class="abs listing">
  <div class="listing-head">Create A Directory ListingToday</div>
  <div class="listing-price display">A$25/Year</div>
  <div class="listing-photo" role="img" aria-label="Sample listing profile card"></div>
  <div class="listing-cap">Sample profile with offer and link</div>
  <span class="abs listing-arrow l"></span><span class="abs listing-arrow r"></span>
  <div class="listing-tier">3 Category Listing</div>
  <div class="listing-desc">Promote Your Special Offers<br>Business Profile &amp; Logo Website<br>&amp; Email Link</div>
</aside>
<nav class="abs categories">
  <span class="active">Banking</span><span>Finance &amp; Insurance</span><span>Marketing Design</span><span>Photography</span><span>Video &amp; Print</span><span>Coaching &amp; Training</span><span>Technology</span><span>Legal</span><span>Administration</span><span class="all">View all Categories</span>
</nav>

<h2 class="abs section-title display" style="top:740px;font-size:50px">Featured Business Offers</h2>
<p class="abs section-sub" style="top:798px">Get Real Support from Our Community.</p>
<div class="abs rule" style="top:830px"></div>

<div class="abs slide-arrow" style="left:175px;top:978px"><svg width="12" height="12"><path d="M9 6H2M5 2L1 6l4 4" stroke="#222" stroke-width="2" fill="none"/></svg></div>
<div class="abs slide-arrow" style="left:974px;top:978px"><svg width="12" height="12"><path d="M3 6h7M7 2l4 4-4 4" stroke="#222" stroke-width="2" fill="none"/></svg></div>

<article class="abs card" style="left:189px">
  <div class="card-img" role="img" aria-label="Hand writing over business charts" style="background:linear-gradient(135deg,#dfe7ef,#9fb3c8)"></div>
  <div class="card-bar">How Did You Sort Your Business <span>→</span></div>
  <p class="card-text">Learn from Dana Ashcroft, a real small business owner. How she started her business and what are the most valuable resources for her right now.</p>
  <div class="more">Read More <svg width="14" height="14"><circle cx="7" cy="7" r="6" fill="none" stroke="#f7931e"/><path d="M6 4l3 3-3 3" stroke="#f7931e" fill="none"/></svg></div>
</article>
<article class="abs card" style="left:462px">
  <div class="card-img" role="img" aria-label="Video still of business ideas sketched on paper" style="background:linear-gradient(135deg,#efe9dc,#c8bfa8);position:relative">
    <svg style="position:absolute;left:96px;top:60px" width="60" height="60"><circle cx="30" cy="30" r="29" fill="#111"/><path d="M23 17l20 13-20 13z" fill="#fff"/></svg>
  </div>
  <div class="card-bar">Why Go with Wattle Business Link? <span>→</span></div>
  <p class="card-text">What small business owner can't relate to the ongoing task of attracting new customers? Struggling with cash flow? Or how about not having enough time in the day? It's obvious that small businesses suffer from a lack of support. And that's where we come in.</p>
  <div class="more">Read More <svg width="14" height="14"><circle cx="7" cy="7" r="6" fill="none" stroke="#f7931e"/><path d="M6 4l3 3-3 3" stroke="#f7931e" fill="none"/></svg></div>
</article>
<article class="abs card" style="left:734px">
  <div class="badge-grid"><span></span><span></span><span></span><span></span><span></span><span></span><span></span><span></span><span></span><span></span><span></span><span></span></div>
  <div class="card-bar">Become an Affiliate <span>→</span></div>
  <p class="card-text">If you have a network of small businesses, let us help to create additional value for your members and make money for your network. Talk to us. today about how we can help.</p>
  <div class="more">Read More <svg width="14" height="14"><circle cx="7" cy="7" r="6" fill="none" stroke="#f7931e"/><path d="M6 4l3 3-3 3" stroke="#f7931e" fill="none"/></svg></div>
</article>
<a class="abs btn" style="left:713px;top:1318px;width:143px;height:39px;background:var(--cyan)">Sign Up for daily Deals</a>
<a class="abs btn" style="left:866px;top:1318px;width:124px;height:39px;background:var(--green)">Submit an offer</a>

<section class="abs promo"></section>
<h2 class="abs section-title promo-title display" style="top:1424px">Austalia's Small Business Directory</h2>
<p class="abs section-sub promo-sub" style="top:1484px">Free Directory Listing, Business Solutions, Business Resources</p>
<div class="abs rule" style="top:1522px;left:460px;width:280px;background:#555"></div>
<div class="abs devices" role="img" aria-label="Smartphones showing directory listings on screen"></div>
<h3 class="abs adv-head display">Advertise your <b>business.</b></h3>
<p class="abs adv-text">Do you sell a product or service? Want to reach Australian Small Business? It's simple and affordable. Starting from just <strong>$2</strong> per day.</p>
<a class="abs btn start">GET STARTED NOW <svg width="16" height="16"><circle cx="8" cy="8" r="7" fill="none" stroke="#111"/><path d="M7 5l3 3-3 3" stroke="#111" fill="none"/></svg></a>

<section class="abs band" role="img" aria-label="Softly blurred cafe interior with warm lamps"></section>
<div class="abs band-col" style="left:189px">
  <h3>Join Us</h3>
  <p>Need a quote, but don't have the time to start the search Let us help you. Tell us what you want and we'll provide you with 3 quotes for you to compare.</p>
  <a class="band-btn">JOIN FREE</a>
</div>
<div class="abs band-col" style="left:626px">
  <h3>Submit an Offer</h3>
  <p>Neque porro quisquam est qui dolorem ipsum quia dolor sit amet, consectetur adipisci velit..."<br>"There is no one who loves pain itself,</p>
  <a class="band-btn">SUBMIT OFFER</a>
</div>

<h2 class="abs section-title display" style="top:2318px;font-size:50px">Get Real Support</h2>
<p class="abs section-sub" style="top:2376px;color:#666">Neque porro quisquam est qui dolorem ipsum</p>
<div class="abs rule" style="top:2408px"></div>

<p class="abs pol-date" style="left:273px">21June 2014</p>
<div class="abs ring-arrow" style="left:252px;top:2610px"><svg width="8" height="8"><path d="M6 1L2 4l4 3" stroke="#999" fill="none"/></svg></div>
<div class="abs polaroid" style="left:273px">
  <div class="frame back1"></div><div class="frame back2"></div><div class="frame"></div>
  <div class="photo" role="img" aria-label="Person working at a desk with a laptop" style="background:linear-gradient(135deg,#6d7f90,#c4a887)"></div>
  <div class="label display">FROM THE VAULT</div>
</div>
<div class="abs ring-arrow" style="left:533px;top:2610px"><svg width="8" height="8"><path d="M2 1l4 3-4 3" stroke="#999" fill="none"/></svg></div>
<p class="abs pol-text" style="left:273px">What is leadership? How does poor leadership affect business? start of blog post or resources post to get them intrested in reading....</p>

<p class="abs pol-date" style="left:703px">Affiliates ABC Brand</p>
<div class="abs ring-arrow" style="left:682px;top:2610px"><svg width="8" height="8"><path d="M6 1L2 4l4 3" stroke="#999" fill="none"/></svg></div>
<div class="abs polaroid" style="left:703px">
  <div class="frame back1"></div><div class="frame back2"></div><div class="frame"></div>
  <div class="photo badge-grid" style="grid-template-columns:repeat(3,1fr);gap:10px"><span></span><span></span><span></span><span></span><span></span><span></span><span></span><span></span><span></span></div>
  <div class="label display">OUR AFFILIATES</div>
</div>
<div class="abs ring-arrow" style="left:953px;top:2610px"><svg width="8" height="8"><path d="M2 1l4 3-4 3" stroke="#999" fill="none"/></svg></div>
<p class="abs pol-text" style="left:703px">We are Collaborating with net-working groups around the country to bring our members more support and greater choice</p>

<footer class="abs site-footer"></footer>
<div class="abs foot-col" style="left:136px"><h4>SITE DIRECTORY:</h4><ul><li>Search the Directory</li><li>Create a Directory Listing</li><li>Quote Finder</li><li>Coupns</li><li>Submit A coupons</li><li>Advertise With Us</li></ul></div>
<div class="abs foot-col" style="left:313px"><h4>RESOURCES:</h4><ul><li>Jointhe Forum</li><li>Submit an Article or Video</li><li>Affiliates</li><li>Become an Affiliate</li><li>Case Studies</li><li>Help Guides</li></ul></div>
<div class="abs foot-col" style="left:489px"><h4>POPULAR CATEGORIES:</h4><ul><li>Lorem ipsum dolor</li><li>Sit amet consec</li><li>Tetur adipiscing elit</li><li>Sed do euismod</li><li>Tempor incidunt</li><li>Magna aliqua</li></ul></div>
<div class="abs foot-col" style="left:684px"><h4>ABOUT:</h4><ul><li>About Us</li><li>Contact Us</li><li>Terms &amp; Conditions</li><li>Privacy Policy</li><li>Supporting City Councils</li><li>Site Map</li></ul></div>
<div class="abs foot-col" style="left:854px"><h4>FOLLOW US:</h4>
  <div class="foot-social"><span style="background:#3b5998"></span><span style="background:#c4302b"></span><span style="background:#3fa9f5"></span><span style="background:#dd4b39"></span><span style="background:#0e76a8"></span></div>
  <a class="coupon-btn">SUBCRIBE COUPON DEALS</a>
</div>
<div class="abs copyright">© Wattle Business Link. All Rights Reserved</div>

</body>
</html>
```